Referral Club PostCard/ Index Card

I need to create an Index card for a Contractor Referral Club. I already did my own door hanger which I can show you. Cost is a factor because I'm just starting my company. You guys have already created my 2 logos when I did a previous logo project so I want to use those logos and colors to create a scheme double sided postcard for my referral club attached to our some examples of other ones I've seen. So, you can 1 of 3 different design/color schemes as a basis:
1) The Black background with Blue Shield
2). The Light Blue background with the white wave (Really like this and the black one)
3). My White background blue/black business card design.
So, 3 different design/color schemes to attack?

You can also look at my website for ideas

http://www.TheParcelKeepersGuild.com
Updates

I have a picture of the things I want to say on BOTH sides on the Index card/[Post card. Basically, there are two versions that can be created, one with the black background/blue logo motif or one with the white/blue background logo. I bought BOTH designs in my logo contest. Actually 1 is the front of the cards and the other is the back of my card. I'm looking for creativity to get these contractors to join this referral club so I can get more leads.

Need extra days to review

I have some new logos,, icons and pdfs to submit for consideration

Target Market(s)

Drawing Other Contractors into my Professional Referral Exchange Club

Industry/Entity Type

Public Insurance Adjusting

Font styles to use
Serif
Sans Serif
Other font styles liked:
• Love Zurich font but very few people have it..It is eye drawing!!

Colors
0054AA
0677BA
7BADD7
CADEEF
E8F1F8
0094D4
00A9DD
6FCCEA
C7EBF8
E9F6FB
EE7325
F08F49
F5BC92
FAE3D3
FDF4ED

Requirements
Must have
• My Blue or Black/White color scheme to stay consistent to what Ive already had done
Nice to have
• Something that jumps off to entice them to join that I haven't thought of.

```html
<!DOCTYPE html>
<html lang="en">
<head>
<meta charset="utf-8">
<title>The Parcel Keeper's Guild – Referral Exchange Club Card</title>
<link rel="stylesheet" href="https://fonts.googleapis.com/css2?family=Arimo:wght@400;700&family=Tinos:wght@400;700&family=Open+Sans:ital,wght@1,600&display=swap">
<style>
  :root{
    --stage:#939598;
    --navy:#1f2a6b;
    --royal:#0054aa;
    --sky:#0094d4;
    --cyan:#00a9dd;
    --orange:#ee7325;
    --red:#e41e26;
    --ink:#111111;
    --grey-text:#6d6e71;
    --white:#ffffff;
    --dark-1:#1a1a1a;
    --light-text:#e6e6e6;
  }
  *{box-sizing:border-box;margin:0;padding:0}
  html,body{width:974px;height:1200px;overflow:hidden;background:var(--stage)}
  .canvas{position:relative;width:974px;height:1200px}
  .card{position:absolute;left:181px;width:617px;height:410px;overflow:hidden;box-shadow:4px 5px 8px rgba(0,0,0,.25)}
  .card-front{top:148px;background:radial-gradient(ellipse at 45% 35%,#ffffff 40%,#e4e4e4 100%)}
  .card-back{top:631px;background:var(--dark-1)}
  .abs{position:absolute}

  /* front */
  .hero-art{left:493px;top:93px;width:124px;height:235px;background:linear-gradient(160deg,#c86b4c 0%,#e9e6e0 22%,#b8bcae 55%,#8f9580 80%,#d9d9d9 100%)}
  .brand-mark{left:290px;top:30px;width:42px;height:42px;border-radius:50%;background:var(--royal)}
  .brand-name{left:181px;width:260px;top:108px;text-align:center;font-family:"Tinos",serif;font-weight:400;color:var(--royal);z-index:2}
  .brand-name .line-1{display:block;font-size:21px;line-height:22px}
  .brand-name .line-2{display:flex;align-items:center;gap:8px;font-family:"Arimo",sans-serif;font-size:15px;line-height:18px;color:var(--sky)}
  .brand-name .line-2::before,.brand-name .line-2::after{content:"";flex:1;height:1.5px;background:var(--royal)}
  .rating{left:470px;top:24px;width:140px;text-align:center;font-family:"Tinos",serif;color:var(--ink);font-size:8.5px;line-height:1.05}
  .rating strong{display:block;font-family:"Arimo",sans-serif;font-size:19px;color:var(--red);font-weight:400;margin-bottom:2px}
  .rating small{font-size:5px;color:#555}
  .club-title{left:0;width:618px;top:166px;text-align:center;font-family:"Arimo",sans-serif;font-weight:400;font-size:23px;color:var(--ink);z-index:2}
  .specialties{left:0;width:449px;top:196px;text-align:right;font-family:"Open Sans",sans-serif;font-style:italic;font-weight:600;font-size:10px;line-height:14px;color:var(--orange);z-index:2}
  .specialties span{display:block}
  .specialties .first{padding-right:40px}
  .join-pill{left:78px;top:235px;width:451px;height:28px;border-radius:14px;background:linear-gradient(90deg,var(--navy) 0%,var(--royal) 55%,var(--cyan) 100%);color:var(--white);font-family:"Arimo",sans-serif;font-size:12.5px;line-height:28px;padding-left:20px;z-index:2}
  .accolade{left:0;width:614px;top:279px;text-align:center;font-family:"Arimo",sans-serif;font-size:12px;color:var(--grey-text);z-index:2}
  .front-wave{left:0;top:270px;width:617px;height:140px;z-index:3}
  .service-area{left:0;width:617px;top:343px;text-align:center;font-family:"Arimo",sans-serif;font-size:12px;color:#dfe6f2;z-index:4}
  .call-line{left:0;width:617px;top:362px;text-align:center;font-family:"Tinos",serif;font-size:27px;color:var(--white);letter-spacing:.5px;z-index:4}

  /* back */
  .back-photo{left:0;top:0;width:617px;height:410px;background:radial-gradient(ellipse at 55% 40%,#4a4a4a 0%,#2a2a2a 55%,#141414 100%)}
  .reasons-title{left:0;width:617px;top:40px;text-align:center;font-family:"Tinos",serif;font-weight:400;font-size:26px;line-height:35px;color:var(--sky)}
  .reasons{left:38px;top:0;list-style:none;font-family:"Arimo",sans-serif;color:var(--light-text);font-size:16px}
  .reason{position:absolute;left:0;width:560px;display:flex;align-items:center;gap:16px;line-height:19px;white-space:nowrap}
  .reason-num{flex:none;width:32px;height:32px;border-radius:50%;border:1.5px solid var(--orange);border-left-color:transparent;display:flex;align-items:center;justify-content:center;font-size:19px;color:var(--white)}
  .reason-1{top:121px}.reason-2{top:173px}.reason-3{top:217px}.reason-4{top:259px}
  .store{font-weight:700;font-size:22px;color:#8a8a8a;margin:0 10px}
  .back-wave{left:0;top:280px;width:617px;height:130px}
  .review-line{left:0;width:556px;top:362px;text-align:center;font-family:"Arimo",sans-serif;font-size:17px;color:var(--ink)}
</style>
</head>
<body>
<main class="canvas">

  <section class="card card-front" aria-label="Card front">
    <div class="abs hero-art" role="img" aria-label="Photo of a small house resting on stacks of banknotes"></div>
    <div class="abs brand-mark"></div>
    <div class="abs brand-name"><span class="line-1">THE PARCEL KEEPER'S</span><span class="line-2">GUILD</span></div>
    <div class="abs rating"><strong>A+ Rating</strong>Highest Rating For<br>Public Insurance Adjusters<br><small>(Source: Review Board)</small></div>
    <h1 class="abs club-title">REFERAL EXCHANGE CLUB</h1>
    <p class="abs specialties"><span class="first">Public Adjusters &amp; Loss Consultants</span><span>Damage Assessors &amp; Certified Insurance Appraisers</span></p>
    <div class="abs join-pill">TO JOIN CLUB CLICK: ProNet &nbsp;| Martin Calloway | Exchange Club</div>
    <p class="abs accolade">Best of the South 8x since 2010</p>
    <svg class="abs front-wave" viewBox="0 0 617 140" preserveAspectRatio="none" aria-hidden="true">
      <defs>
        <linearGradient id="frontBand" x1="0" x2="1" y1="0" y2="0">
          <stop offset="0" stop-color="#1f2a6b"/>
          <stop offset=".5" stop-color="#0054aa"/>
          <stop offset="1" stop-color="#13a3dc"/>
        </linearGradient>
      </defs>
      <path d="M0 36 C100 22 200 30 300 50 C400 66 500 40 617 2 L617 140 L0 140 Z" fill="#111"/>
      <path d="M0 40 C100 28 200 36 300 56 C400 72 500 50 617 18 L617 140 L0 140 Z" fill="url(#frontBand)"/>
    </svg>
    <p class="abs service-area">Servicing Florida, Georgia, Alabama and Mississippi</p>
    <p class="abs call-line">CALL 1-800-PARCELS</p>
  </section>

  <section class="card card-back" aria-label="Card back">
    <div class="abs back-photo" role="img" aria-label="Dim dark background photo of banknotes"></div>
    <h2 class="abs reasons-title">TOP FOUR REASONS<br>FOR JOINING THE CLUB</h2>
    <ol class="abs reasons">
      <li class="reason reason-1"><span class="reason-num">1</span>EXCLUSIVITY ONLY ONE PER INDUSTRY PER REGION</li>
      <li class="reason reason-2"><span class="reason-num">2</span>GUARANTEED RETURN REFERRAL “ACCOUNTABILITY”</li>
      <li class="reason reason-3"><span class="reason-num">3</span>$75 GIFT CERTIFICATE <span class="store">Greenmart</span> OR <span class="store">ValueHub</span></li>
      <li class="reason reason-4"><span class="reason-num">4</span>TRUST YOUR CLIENT HAS THE BEST LOCAL<br>PUBLIC ADMINISTER</li>
    </ol>
    <svg class="abs back-wave" viewBox="0 0 617 130" preserveAspectRatio="none" aria-hidden="true">
      <path d="M0 14 C120 18 220 32 330 42 C420 50 520 44 617 38 L617 130 L0 130 Z" fill="#0094d4"/>
      <path d="M0 34 C150 38 250 56 340 58 C450 60 540 46 617 38 L617 130 L0 130 Z" fill="#111"/>
      <path d="M0 40 C150 44 250 62 340 64 C450 66 540 52 617 44 L617 130 L0 130 Z" fill="#fff"/>
    </svg>
    <p class="abs review-line">COMPLIMENTARY POLICY &amp; CLAIM REVIEW</p>
  </section>

</main>
</body>
</html>
```